Mobile Friendly Lead Generation Landing Page

We are a web marketing company that specialized in web lead generation. Recently we have started buying media from mobile devices and we need a mobile interface(landing page) where we can collect user data in an effective manner.

Our current mobile landing page is:
http://www.tutorpath.example.com/lp13d/index.aspx?a=true&source=841356
Through this you can see what the steps/questions users need to answer to get matched to a school. We need the design for the whole process.

We are pretty open for design ideas and our goal is to make this mobile optimized landing page have the look and feel of an app...but not an app.
There are several questions in the process but we are open to changing the way they are presented. As in, you can have one question at a time or a few.
The goal is to make this EXTREMELY EASY for users to interact with.

One example that we have liked is:
http://learnvane.example/schools/57214-page1.lvne (please note that this opens only on mobile devices)

Some of these screenshots are attached.

Our web form looks like this:
http://www.tutorpath.example.com/lp88/index.aspx?a=true

```html
<!DOCTYPE html>
<html lang="en">
<head>
<meta charset="utf-8">
<title>Main Screen Revisions 6 and 7</title>
<link rel="stylesheet" href="https://fonts.googleapis.com/css2?family=Roboto:wght@300;400&display=swap">
<style>
  :root {
    --bg-green: #c9f3c2;
    --bg-cream: #f8f6df;
    --bg-blue: #c6e3f6;
    --brand-blue: #1a82f7;
    --brand-red: #ee1c1c;
    --ink: #333333;
    --ink-soft: #4a4a4a;
    --rule: #e2e2e2;
    --chrome: #f6f6f6;
    --field: #dcdcdc;
    --chevron: #9a9a9a;
    --white: #ffffff;
  }
  * { box-sizing: border-box; margin: 0; padding: 0; }
  html, body { width: 1200px; height: 840px; overflow: hidden; }
  body {
    position: relative;
    font-family: "Roboto", "Helvetica Neue", Arial, sans-serif;
    color: var(--ink);
    background: linear-gradient(135deg, var(--bg-green) 0%, var(--bg-cream) 35%, var(--bg-cream) 60%, var(--bg-blue) 100%);
  }
  .screen {
    position: absolute;
    top: 135px;
    width: 298px;
    height: 527px;
    background: var(--white);
    overflow: hidden;
    box-shadow: 0 0 0 1px rgba(0,0,0,.06);
  }
  .screen--rev6 { left: 214px; }
  .screen--rev7 { left: 674px; }

  .status-bar {
    height: 17px;
    display: flex;
    align-items: center;
    padding: 0 6px;
    font-size: 10.5px;
    color: #111;
    background: var(--chrome);
  }
  .status-bar .carrier { display: flex; align-items: center; gap: 4px; width: 110px; }
  .status-bar .time { flex: 1; text-align: left; }
  .status-bar .battery { display: flex; align-items: center; gap: 3px; }

  .address-bar {
    height: 43px;
    background: var(--chrome);
    padding: 6px 10px 0;
  }
  .address-field {
    position: relative;
    height: 26px;
    border-radius: 5px;
    background: var(--field);
    font-size: 15px;
    line-height: 26px;
    text-align: center;
    color: #222;
  }
  .address-field svg { position: absolute; right: 8px; top: 6px; }

  .blur-strip {
    height: 18px;
    background: linear-gradient(90deg, #eec9c5 0%, #e9d7cf 40%, #d7ebe3 75%, #dfeee8 100%);
  }
  .blur-strip--mid { height: 20px; background: linear-gradient(90deg, #e7c7cb 0%, #e6d8d8 45%, #d8ece6 100%); }
  .blur-strip--foot { height: 22px; background: linear-gradient(90deg, #cbd7ef 0%, #e3e6ee 50%, #f3ead1 100%); }

  .banner {
    height: 40px;
    display: flex;
    align-items: center;
    justify-content: center;
    font-size: 14px;
    color: var(--white);
    letter-spacing: .1px;
    padding: 0 7px;
  }
  .banner--cta { background: var(--brand-blue); }
  .banner--section { background: var(--brand-red); }
  .screen--rev7 .banner { justify-content: space-between; }

  .grant-note {
    height: 41px;
    display: flex;
    align-items: center;
    justify-content: center;
    font-size: 12.5px;
    color: var(--ink-soft);
    border-bottom: 1px solid var(--rule);
  }

  .interest-list { list-style: none; }
  .interest-item {
    position: relative;
    height: 41px;
    display: flex;
    align-items: center;
    padding-left: 48px;
    font-size: 12.5px;
    color: var(--ink);
  }
  .interest-item::after {
    content: "";
    position: absolute;
    left: 14px; right: 0; bottom: 0;
    border-bottom: 1px solid var(--rule);
  }
  .interest-item:last-child::after { left: 0; }
  .interest-icon {
    position: absolute;
    left: 15px;
    top: 9px;
    width: 22px;
    height: 22px;
    color: var(--brand-blue);
  }
  .screen--rev7 .interest-icon {
    left: 12px; top: 6px;
    width: 28px; height: 28px;
    border-radius: 50%;
    background: var(--brand-blue);
    color: var(--white);
    padding: 5px;
  }
  .screen--rev7 .interest-item { padding-left: 49px; }
  .interest-icon svg { width: 100%; height: 100%; display: block; }
  .chevron { position: absolute; right: 14px; top: 13px; color: var(--chevron); }

  .toolbar {
    height: 41px;
    display: flex;
    align-items: center;
    justify-content: space-around;
    background: var(--chrome);
    border-top: 1px solid #d8d8d8;
    color: var(--brand-blue);
  }
  .toolbar .is-disabled { color: #b9b9b9; }

  .caption {
    position: absolute;
    top: 790px;
    width: 400px;
    text-align: center;
    font-size: 24px;
    font-weight: 300;
    color: #3a3a3a;
  }
  .caption--rev6 { left: 162px; }
  .caption--rev7 { left: 627px; }
</style>
</head>
<body>

<svg width="0" height="0" style="position:absolute" aria-hidden="true">
  <defs>
    <symbol id="icon-brush" viewBox="0 0 24 24" fill="none" stroke="currentColor" stroke-width="1.5" stroke-linejoin="round" stroke-linecap="round">
      <path d="M21 3 11.5 13.5"/><path d="M11.5 13.5c-3-1-5 1-5 3.5 0 2-1.5 3-3.5 3.5 4.5 1 9 0 9.5-4.5z"/>
    </symbol>
    <symbol id="icon-briefcase" viewBox="0 0 24 24" fill="none" stroke="currentColor" stroke-width="1.5">
      <rect x="2.5" y="7" width="19" height="13" rx="1"/><path d="M9 7V4.5h6V7M2.5 12.5h19"/>
    </symbol>
    <symbol id="icon-gavel" viewBox="0 0 24 24" fill="none" stroke="currentColor" stroke-width="1.5" stroke-linejoin="round">
      <path d="M6 4.5 11.5 2l2.5 5L8.5 9.5z"/><path d="M11 6.5 21 12"/><path d="M3 20h11v-2.5H3z"/>
    </symbol>
    <symbol id="icon-abc" viewBox="0 0 24 24" fill="currentColor">
      <text x="12" y="10" text-anchor="middle" font-family="Roboto, sans-serif" font-size="9">ABC</text>
      <rect x="2" y="12" width="20" height="1"/>
      <text x="12" y="22" text-anchor="middle" font-family="Roboto, sans-serif" font-size="9">1 2 3</text>
    </symbol>
    <symbol id="icon-compass" viewBox="0 0 24 24" fill="none" stroke="currentColor" stroke-width="1.5" stroke-linecap="round">
      <circle cx="12" cy="4" r="1.8"/><path d="M11 6 4.5 22M13 6l6.5 16M6 16.5h12"/>
    </symbol>
    <symbol id="icon-book" viewBox="0 0 24 24" fill="none" stroke="currentColor" stroke-width="1.5" stroke-linejoin="round">
      <path d="M2.5 6q4.5-2 9.5 0v13q-5-2-9.5 0zM12 6q5-2 9.5 0v13q-4.5-2-9.5 0z"/>
    </symbol>
    <symbol id="icon-chevron" viewBox="0 0 12 12" fill="none" stroke="currentColor" stroke-width="1.6" stroke-linecap="round" stroke-linejoin="round">
      <path d="M4 2l4 4-4 4"/>
    </symbol>
    <symbol id="icon-reload" viewBox="0 0 14 14" fill="none" stroke="#333" stroke-width="1.4">
      <path d="M11.5 7A4.5 4.5 0 1 1 7 2.5h2.5"/><path d="M8 0.5l2 2-2 2"/>
    </symbol>
    <symbol id="icon-wifi" viewBox="0 0 14 10" fill="none" stroke="#111" stroke-width="1.3">
      <path d="M1 4a9 9 0 0 1 12 0M3 6a6 6 0 0 1 8 0M5 8a3 3 0 0 1 4 0"/>
    </symbol>
    <symbol id="icon-back" viewBox="0 0 24 24" fill="none" stroke="currentColor" stroke-width="1.6" stroke-linecap="round" stroke-linejoin="round"><path d="M15 3 7 12l8 9"/></symbol>
    <symbol id="icon-forward" viewBox="0 0 24 24" fill="none" stroke="currentColor" stroke-width="1.6" stroke-linecap="round" stroke-linejoin="round"><path d="M9 3l8 9-8 9"/></symbol>
    <symbol id="icon-share" viewBox="0 0 24 24" fill="none" stroke="currentColor" stroke-width="1.4" stroke-linejoin="round"><path d="M9 9H5v13h14V9h-4M12 15V2M8 6l4-4 4 4"/></symbol>
    <symbol id="icon-bookmarks" viewBox="0 0 24 24" fill="none" stroke="currentColor" stroke-width="1.4" stroke-linejoin="round"><path d="M1.5 5q5-2 10.5 1v14q-5.5-3-10.5-1zM12 6q5.5-3 10.5-1v14q-5-2-10.5 1z"/></symbol>
    <symbol id="icon-tabs" viewBox="0 0 24 24" fill="none" stroke="currentColor" stroke-width="1.4"><rect x="2" y="7" width="15" height="15"/><path d="M7 7V2h15v15h-5"/></symbol>
  </defs>
</svg>

<!-- Revision 6 -->
<section class="screen screen--rev6">
  <div class="status-bar">
    <span class="carrier">●●●○○ Nexcell <svg width="14" height="10"><use href="#icon-wifi"/></svg></span>
    <span class="time">4:21 PM</span>
    <span class="battery">100% <svg width="22" height="10"><rect x="0.5" y="0.5" width="19" height="9" rx="1.5" fill="none" stroke="#111"/><rect x="2" y="2" width="16" height="6" fill="#111"/><rect x="20" y="3" width="1.5" height="4" fill="#111"/></svg></span>
  </div>
  <div class="address-bar"><div class="address-field">tutorpath.example.com<svg width="14" height="14"><use href="#icon-reload"/></svg></div></div>
  <div class="blur-strip"></div>
  <div class="banner banner--cta">COMPLETE OUR 3-MINUTE APP</div>
  <div class="grant-note">Get up to $5, 645* per year in Grants if you qualify</div>
  <div class="blur-strip blur-strip--mid"></div>
  <div class="banner banner--section">SELECT AREA OF YOUR INTEREST</div>
  <ul class="interest-list">
    <li class="interest-item"><span class="interest-icon"><svg><use href="#icon-brush"/></svg></span>Art &amp; Design<svg class="chevron" width="12" height="12"><use href="#icon-chevron"/></svg></li>
    <li class="interest-item"><span class="interest-icon"><svg><use href="#icon-briefcase"/></svg></span>Business<svg class="chevron" width="12" height="12"><use href="#icon-chevron"/></svg></li>
    <li class="interest-item"><span class="interest-icon"><svg><use href="#icon-gavel"/></svg></span>Criminal Justice<svg class="chevron" width="12" height="12"><use href="#icon-chevron"/></svg></li>
    <li class="interest-item"><span class="interest-icon"><svg><use href="#icon-abc"/></svg></span>Education &amp; Teaching<svg class="chevron" width="12" height="12"><use href="#icon-chevron"/></svg></li>
    <li class="interest-item"><span class="interest-icon"><svg><use href="#icon-compass"/></svg></span>Engineering<svg class="chevron" width="12" height="12"><use href="#icon-chevron"/></svg></li>
    <li class="interest-item"><span class="interest-icon"><svg><use href="#icon-book"/></svg></span>Other<svg class="chevron" width="12" height="12"><use href="#icon-chevron"/></svg></li>
  </ul>
  <div class="blur-strip blur-strip--foot"></div>
  <nav class="toolbar">
    <svg width="22" height="22"><use href="#icon-back"/></svg>
    <svg class="is-disabled" width="22" height="22"><use href="#icon-forward"/></svg>
    <svg width="22" height="22"><use href="#icon-share"/></svg>
    <svg width="24" height="24"><use href="#icon-bookmarks"/></svg>
    <svg width="22" height="22"><use href="#icon-tabs"/></svg>
  </nav>
</section>

<!-- Revision 7 -->
<section class="screen screen--rev7">
  <div class="status-bar">
    <span class="carrier">●●●○○ Nexcell <svg width="14" height="10"><use href="#icon-wifi"/></svg></span>
    <span class="time">4:21 PM</span>
    <span class="battery">100% <svg width="22" height="10"><rect x="0.5" y="0.5" width="19" height="9" rx="1.5" fill="none" stroke="#111"/><rect x="2" y="2" width="16" height="6" fill="#111"/><rect x="20" y="3" width="1.5" height="4" fill="#111"/></svg></span>
  </div>
  <div class="address-bar"><div class="address-field">tutorpath.example.com<svg width="14" height="14"><use href="#icon-reload"/></svg></div></div>
  <div class="blur-strip"></div>
  <div class="banner banner--cta">COMPLETE OUR 3-MINUTE APP
    <svg width="24" height="24" viewBox="0 0 24 24" fill="none" stroke="#fff" stroke-width="1.3"><circle cx="12" cy="12" r="10.5"/><path d="M12 6v6.5H7.5"/></svg>
  </div>
  <div class="grant-note">Get up to $5, 645* per year in Grants if you qualify</div>
  <div class="blur-strip blur-strip--mid"></div>
  <div class="banner banner--section">SELECT AREA OF YOUR INTEREST
    <svg width="22" height="16" viewBox="0 0 22 16" fill="#fff"><rect y="0" width="22" height="3"/><rect y="6.5" width="22" height="3"/><rect y="13" width="22" height="3"/></svg>
  </div>
  <ul class="interest-list">
    <li class="interest-item"><span class="interest-icon"><svg><use href="#icon-brush"/></svg></span>Art &amp; Design<svg class="chevron" width="12" height="12"><use href="#icon-chevron"/></svg></li>
    <li class="interest-item"><span class="interest-icon"><svg><use href="#icon-briefcase"/></svg></span>Business<svg class="chevron" width="12" height="12"><use href="#icon-chevron"/></svg></li>
    <li class="interest-item"><span class="interest-icon"><svg><use href="#icon-gavel"/></svg></span>Criminal Justice<svg class="chevron" width="12" height="12"><use href="#icon-chevron"/></svg></li>
    <li class="interest-item"><span class="interest-icon"><svg><use href="#icon-abc"/></svg></span>Education &amp; Teaching<svg class="chevron" width="12" height="12"><use href="#icon-chevron"/></svg></li>
    <li class="interest-item"><span class="interest-icon"><svg><use href="#icon-compass"/></svg></span>Engineering<svg class="chevron" width="12" height="12"><use href="#icon-chevron"/></svg></li>
    <li class="interest-item"><span class="interest-icon"><svg><use href="#icon-book"/></svg></span>Other<svg class="chevron" width="12" height="12"><use href="#icon-chevron"/></svg></li>
  </ul>
  <div class="blur-strip blur-strip--foot"></div>
  <nav class="toolbar">
    <svg width="22" height="22"><use href="#icon-back"/></svg>
    <svg class="is-disabled" width="22" height="22"><use href="#icon-forward"/></svg>
    <svg width="22" height="22"><use href="#icon-share"/></svg>
    <svg width="24" height="24"><use href="#icon-bookmarks"/></svg>
    <svg width="22" height="22"><use href="#icon-tabs"/></svg>
  </nav>
</section>

<p class="caption caption--rev6">Main Screen Revision 6</p>
<p class="caption caption--rev7">Main Screen Revision 7</p>

</body>
</html>
```